Home brewer beer bottle label

I need a label for home-brew beer bottles. My sons and I all make our own beer. It should say Tarrin Brew in blackletter (because we are of German heritage) (EDIT: ACTUALLY WE ARE LIKING OTHER TYPEFACE NOW) and the designer will need to work in aspects of the Tarrin family (crest attached). Finally we will need two blank areas or lines for (1) what kind of beer (handwritten) and (2) who made it (the Beerista!) I have attached a rough sketch, but feel free to ignore and be creative. No color requirements. (EDIT: ACTUALLY, MY WIFE LIKES THE LITTLE BIT OF PURPLE IN THE 4TH DESIGN) Would like the logotype portion of the label to be usable on its own as a family logo. (EDIT; THIS IS LESS IMPORTANT NOW). I have attached another file sketch, which shows using the parts of the family crest w/out trying to replicate it. Thanks, everyone, for the good work....

Reason: Extending because my wife is out of town until Wednesday and I need her input.

Target Market(s)

Mostly friends and family at the wedding.

Industry/Entity Type

Work

Font styles to use
Serif
Sans Serif

Requirements
Must have
• Tightly kerned lettering,
Nice to have
• Color, one Group of Elements in Indesign and the print file, "Beer" and "Beerista" lines
Should not have
• Hard to see logo or logo type

```html
<!DOCTYPE html>
<html lang="en">
<head>
<meta charset="utf-8">
<title>Tarrin Brew – Bottle Label</title>
<link rel="stylesheet" href="https://fonts.googleapis.com/css2?family=Almendra:wght@700&family=Fira+Sans+Condensed:wght@700&display=swap">
<style>
  :root {
    --label-tan: #cfc785;
    --ink: #1a1715;
    --band-blue: #3a4ba0;
    --crest-blue: #3457b0;
    --crest-gold: #e2b64a;
    --page: #ffffff;
  }
  html, body {
    margin: 0;
    padding: 0;
    width: 988px;
    height: 1200px;
    overflow: hidden;
    background: var(--page);
  }
  .label {
    position: relative;
    width: 988px;
    height: 1200px;
  }
  .label-shape {
    position: absolute;
    inset: 0;
  }
  .label-shape .body { fill: var(--label-tan); }
  .label-shape .frame {
    fill: none;
    stroke: var(--ink);
    stroke-width: 10;
    stroke-linejoin: miter;
  }
  .family-crest {
    position: absolute;
    left: 250px;
    top: 100px;
    width: 496px;
    height: 490px;
    border-radius: 46% 46% 40% 40%;
    background: radial-gradient(ellipse at 50% 55%, var(--crest-blue) 0%, var(--crest-blue) 38%, var(--crest-gold) 75%, var(--label-tan) 100%);
  }
  .brand-name {
    position: absolute;
    left: 0;
    top: 600px;
    width: 988px;
    margin: 0;
    text-align: center;
    font-family: "Almendra", serif;
    font-weight: 700;
    font-size: 182px;
    line-height: 188px;
    letter-spacing: -3px;
    color: var(--ink);
  }
  .brand-name span { display: block; }
  .tagline-band {
    position: absolute;
    left: 40px;
    top: 1003px;
    width: 908px;
    height: 67px;
    background: var(--band-blue);
    display: flex;
    align-items: center;
    justify-content: center;
  }
  .tagline {
    margin: 0;
    font-family: "Fira Sans Condensed", sans-serif;
    font-weight: 700;
    font-size: 43px;
    color: var(--label-tan);
  }
  .fill-line {
    position: absolute;
    top: 1090px;
    margin: 0;
    font-family: "Fira Sans Condensed", sans-serif;
    font-weight: 700;
    font-size: 42px;
    color: var(--ink);
  }
  .fill-line.beer-type { left: 62px; }
  .fill-line.brewer { left: 527px; }
</style>
</head>
<body>
  <div class="label">
    <svg class="label-shape" width="988" height="1200" viewBox="0 0 988 1200" aria-hidden="true">
      <path class="body" d="M0 398 H118 V380 A376 376 0 0 1 870 380 V398 H988 V1200 H0 Z"/>
      <path class="frame" d="M30 425 H143 V380 A351 351 0 0 1 845 380 V425 H958 V1170 H30 Z"/>
    </svg>

    <div class="family-crest" role="img" aria-label="Family coat of arms"></div>

    <h1 class="brand-name"><span>Tarrin</span><span>Brew</span></h1>

    <div class="tagline-band">
      <p class="tagline">Home-Brewed by the Tarrin Family</p>
    </div>

    <p class="fill-line beer-type">Beer</p>
    <p class="fill-line brewer">Beerista</p>
  </div>
</body>
</html>
```